Brell Stone Company Business Cards

Front and Back Business Card - logo and text setup - cool design. I need workable photoshop or illustrator files so I can setup each employee card with design that is created
Updates

Hi everyone, thank you for the great entries. Please no more white and blue cards - there are so many already - black and silver only now please. thanks!

Target Market(s)

Construction Industry - Facility Managers

Industry/Entity Type

Construction

Contact Information for Business Card

I really like contemporary simplistic looks - clean neat....not opposed to seeing some black backrounds

Requirements
Must have
• Logo/website address with design on front only - www.brellstone-example.com (logo attached)
• Back:
• Name/Title/Company Address/Phone/email address
Nice to have
• Cool design
Should not have
• Nothing gimmicky like Fire or Water - since we are a Fire Protection company - it has all been done

```html
<!DOCTYPE html>
<html lang="en">
<head>
<meta charset="utf-8">
<title>Brell Stone Company Business Cards</title>
<link rel="stylesheet" href="https://fonts.googleapis.com/css2?family=Open+Sans:wght@400;700;800&display=swap">
<style>
  :root {
    --backdrop: #c3c7cb;
    --card-dark: #000000;
    --card-mid: #1a1a1a;
    --brand-blue: #0322a0;
    --brand-red: #fe2020;
    --ink-light: #ffffff;
  }
  html, body {
    margin: 0;
    padding: 0;
    width: 1200px;
    height: 1193px;
    overflow: hidden;
    background: var(--backdrop);
    font-family: "Open Sans", Arial, sans-serif;
  }
  .canvas { position: relative; width: 1200px; height: 1193px; }
  .card {
    position: absolute;
    width: 872px;
    height: 498px;
    border-radius: 42px;
    overflow: hidden;
    background: linear-gradient(180deg, var(--card-dark) 0%, var(--card-mid) 50%, var(--card-dark) 100%);
  }
  .card--contact { left: 78px; top: 80px; }
  .card--brand { left: 249px; top: 637px; }

  .wordmark {
    position: absolute;
    margin: 0;
    font-weight: 800;
    color: var(--brand-red);
    white-space: nowrap;
    letter-spacing: -1px;
    transform: translate(-50%, -50%);
  }
  .card--contact .wordmark { left: 250px; top: 252px; font-size: 58px; }
  .card--brand .wordmark { left: 440px; top: 244px; font-size: 92px; }

  .web-strip {
    position: absolute;
    left: 481px; top: 86px;
    width: 40px; height: 331px;
    background: var(--brand-red);
  }
  .web-strip__text {
    position: absolute;
    left: 50%; top: 50%;
    transform: translate(-50%, -50%) rotate(-90deg);
    color: var(--ink-light);
    font-size: 17px;
    letter-spacing: 2px;
    white-space: nowrap;
  }
  .details {
    position: absolute;
    left: 526px; top: 86px;
    width: 346px; height: 331px;
    background: var(--brand-blue);
    color: var(--ink-light);
    box-sizing: border-box;
    padding: 26px 0 0 21px;
  }
  .details__name { margin: 0; font-size: 30px; font-weight: 700; line-height: 36px; }
  .details__title { margin: 0; font-size: 26px; line-height: 34px; }
  .details__line {
    display: flex; align-items: center; gap: 12px;
    font-size: 22.5px; line-height: 30px; margin: 0;
  }
  .details__line--phone { margin-top: 26px; }
  .details__line--email { margin-top: 12px; }
  .details__line svg { width: 24px; height: 24px; flex: none; }
  .details__address { margin: 28px 0 0; font-size: 23px; line-height: 35px; font-style: normal; }

  .back-web {
    position: absolute;
    left: 0; right: 0; top: 436px;
    text-align: center;
    color: var(--ink-light);
    font-size: 27px;
    letter-spacing: 5px;
  }
</style>
</head>
<body>
<main class="canvas">
  <section class="card card--contact">
    <p class="wordmark">Brell Stone</p>
    <div class="web-strip"><span class="web-strip__text">www.brellstone-example.com</span></div>
    <div class="details">
      <h1 class="details__name">Dana Whitfield</h1>
      <p class="details__title">President</p>
      <p class="details__line details__line--phone">
        <svg viewBox="0 0 24 24" aria-hidden="true"><path fill="#fff" d="M6.6 2.5l3 3.4-2 2.2c1.3 2.9 3.4 5 6.3 6.3l2.2-2 3.4 3-1.9 3.1C11.8 18.8 5.2 12.2 3.5 4.4z"/><path d="M14 3a7 7 0 0 1 7 7M14 6.5a3.5 3.5 0 0 1 3.5 3.5" stroke="#fff" stroke-width="1.6" fill="none"/></svg>
        (555) 014-2087
      </p>
      <p class="details__line details__line--email">
        <svg viewBox="0 0 24 24" aria-hidden="true"><rect x="1" y="5" width="22" height="14" fill="#fff"/><path d="M1 5l11 8 11-8M1 19l8-7M23 19l-8-7" stroke="#0322a0" stroke-width="1.6" fill="none"/></svg>
        info@brellstone-example.com
      </p>
      <address class="details__address">48 Meridian Way<br>Harbor Point, NY 10999</address>
    </div>
  </section>

  <section class="card card--brand">
    <p class="wordmark">Brell Stone</p>
    <p class="back-web">www.brellstone-example.com</p>
  </section>
</main>
</body>
</html>
```